Transform Your Giving

I need a tri-fold brochure that will fit in a standard number 10 business envelope. Meadowlark and Allied Services is a charitable nonprofit. The goal of this brochure is to stimulate people into thinking about other ways to make a donation. The design should communicate the essential information on donation options, create a sense of professional integrity, be graphically sharp, easy to read and laid out in a way that doesn't make the material appear crowded.

```html
<!DOCTYPE html>
<html lang="en">
<head>
<meta charset="utf-8">
<title>Transform Your Giving – Tri-fold Brochure</title>
<link rel="stylesheet" href="https://fonts.googleapis.com/css2?family=Montserrat:ital,wght@0,300;0,400;0,500;0,600;0,700;0,800;1,400&display=swap">
<style>
:root{
  --navy:#2b2a6b;
  --green:#4cb748;
  --green-dark:#3fa33b;
  --white:#ffffff;
  --paper:#ececec;
  --paper-light:#f4f4f4;
  --stage:#9a9a9a;
  --ink:#3a3a3a;
}
*{box-sizing:border-box;margin:0;padding:0}
html,body{width:1200px;height:1200px;overflow:hidden;background:var(--stage);font-family:"Montserrat",sans-serif}
.sheet{position:absolute;left:255px;width:660px;height:513px;overflow:hidden}
.sheet--outside{top:65px;background:var(--white)}
.sheet--inside{top:621px;background:var(--paper)}
.panel{position:absolute;top:0;height:513px}
.abs{position:absolute}
.center{text-align:center}

/* outside: impact panel */
.impact{left:0;width:216px;background:var(--white)}
.impact__title{top:20px;left:0;width:216px;font-weight:800;font-size:15.5px;line-height:19px;color:var(--navy)}
.impact__title span{color:var(--green);display:block}
.impact__text{top:64px;left:22px;width:172px;font-size:7.6px;line-height:9.8px;color:var(--ink)}
.checklist{top:156px;left:45px;width:132px;list-style:none}
.checklist li{height:16px;margin-bottom:5.2px;border:1px solid var(--green);display:flex;align-items:center;justify-content:center;gap:4px;font-size:8.4px;color:var(--ink)}
.checklist svg{width:8px;height:8px;color:var(--green)}

/* outside: contact panel */
.contact{left:216px;width:217px;background:var(--green);color:var(--white)}
.brandmark{display:flex;align-items:center;justify-content:center;gap:6px;font-weight:800;text-transform:uppercase;letter-spacing:.3px}
.brandmark i{display:block;border-radius:50%;flex:none}
.contact .brandmark{top:26px;left:0;width:217px;font-size:11px;line-height:13px;color:var(--white)}
.contact .brandmark i{width:14px;height:14px;background:var(--white)}
.contact__intro{top:90px;left:18px;width:181px;font-size:9.2px;line-height:11px;font-weight:500}
.quote{top:190px;left:33px;width:157px;height:48px;border:1px solid var(--white);border-radius:7px;padding:9px 6px 0;font-size:6.8px;line-height:9px}
.quote em{display:block;font-style:italic}
.quote b{display:block;margin-top:2px;font-weight:700}
.quote__mark{top:178px;left:94px;width:30px;height:18px;background:var(--green);font-size:26px;line-height:26px;font-weight:800;text-align:center}
.will{top:246px;left:0;width:217px;line-height:11px}
.will__lead{font-size:8px;font-weight:500}
.will__url{font-size:13px;font-weight:800;line-height:17px}
.will__note{font-size:8px;font-weight:400}
.will__free{font-size:9px;font-weight:800}
.pill-contact{top:316px;left:60px;width:98px;height:17px;border-radius:9px;background:var(--navy);font-weight:800;font-size:10.5px;line-height:17px}
.contact__ask{top:339px;left:0;width:217px}
.contact__ask b{display:block;font-size:10.5px;font-weight:800;color:var(--navy)}
.contact__ask span{display:block;font-size:8px;line-height:10px}
.details{top:378px;left:56px;list-style:none}
.details li{display:flex;align-items:center;gap:6px;height:23px;font-size:6.7px;line-height:8px}
.details li b{font-weight:700}
.details .ic{width:18px;height:18px;border:1px solid var(--white);border-radius:50%;display:flex;align-items:center;justify-content:center;flex:none}
.details .ic svg{width:10px;height:10px;color:var(--white)}
.follow{top:452px;left:0;width:217px;display:flex;justify-content:center;align-items:center;gap:4px;font-size:8px;font-weight:500}
.follow i{display:block;width:11px;height:11px;border-radius:50%;background:var(--white)}
.follow i + i{background:var(--navy)}
.disclaimer{top:476px;left:22px;width:173px;font-size:3.6px;line-height:4.6px}

/* outside: cover panel */
.cover{left:433px;width:227px;background:var(--navy)}
.cover__art{top:0;left:0}
.cover__title{top:218px;left:0;width:227px;color:var(--white);font-weight:800;font-size:17px;line-height:19px}
.cover__title span{display:block;color:var(--green);font-size:24.5px;line-height:27px}
.cover__ticks{top:270px;left:20px;width:188px;height:22px;border-top:1px solid rgba(255,255,255,.6);border-bottom:1px solid rgba(255,255,255,.6);display:flex;align-items:center;justify-content:center;gap:8px;color:var(--white);font-weight:800;font-size:11px}
.cover__ticks span{display:flex;align-items:center;gap:3px}
.cover__ticks svg{width:12px;height:12px;color:var(--green)}
.cover__lead{top:298px;left:10px;width:207px;color:var(--white);font-weight:700;font-size:7.6px;line-height:10px}
.options{top:328px;left:11px;width:206px;display:flex;justify-content:space-between;list-style:none}
.options li{width:38px;text-align:center;color:var(--white);font-size:5.2px;font-weight:700;line-height:6.4px}
.options svg{display:block;margin:0 auto 3px;width:28px;height:28px;color:var(--green)}
.cover .brandmark{top:462px;left:0;width:227px;font-size:11px;line-height:13px;color:var(--navy)}
.cover .brandmark i{width:16px;height:16px;background:var(--green)}

/* inside */
.inside__art{top:0;left:0}
.mid-panel{position:absolute;left:220px;top:0;width:220px;height:513px;background:var(--paper-light)}
.badge{top:42px;left:23px;width:226px;height:80px}
.badge__num{top:48px;left:40px;font-size:66px;line-height:66px;font-weight:800;color:var(--green)}
.badge__text{top:50px;left:100px;font-size:18.5px;line-height:18.5px;font-weight:800;color:var(--white)}
.way{position:absolute}
.way__head{display:flex;gap:6px;align-items:flex-start}
.way__icon{width:64px;height:64px;border-radius:50%;background:var(--navy);display:flex;align-items:center;justify-content:center;flex:none}
.way__icon svg{width:34px;height:34px;color:var(--white)}
.way__titles{padding-top:2px}
.way__titles h2{font-size:10.6px;line-height:13px;font-weight:700;color:var(--navy)}
.way__titles p{margin-top:2px;font-size:5.3px;line-height:6.6px;font-weight:700;color:var(--green)}
.way__body{margin-top:6px;font-size:5.3px;line-height:7px;color:var(--ink);font-weight:400}
.how{display:inline-block;margin:6px 0 5px;padding:0 5px;height:11px;line-height:11px;border-radius:3px;background:var(--green);color:var(--white);font-size:6px;font-weight:500}
.ticks{list-style:none;margin:6px 0 4px}
.ticks li{display:flex;gap:5px;margin-bottom:7px;padding-right:6px}
.ticks svg{width:10px;height:10px;flex:none;color:var(--green)}
.inside .brandmark{top:453px;left:220px;width:220px;font-size:11px;line-height:13px;color:var(--navy)}
.inside .brandmark i{width:16px;height:16px;background:var(--green)}
.inside__arc{top:412px;left:220px}
</style>
</head>
<body>

<svg width="0" height="0" style="position:absolute" aria-hidden="true">
  <defs>
    <symbol id="ic-check" viewBox="0 0 20 20"><g fill="none" stroke="currentColor" stroke-width="1.8" stroke-linecap="round" stroke-linejoin="round"><path d="M17 9.5A7.5 7.5 0 1 1 13 3.3"/><path d="M6.5 9.5l3 3 7-8"/></g></symbol>
    <symbol id="ic-coin" viewBox="0 0 40 40"><g fill="none" stroke="currentColor" stroke-width="1.8"><circle cx="20" cy="20" r="17"/><circle cx="20" cy="20" r="12"/><path d="M16 14h5.5a3 3 0 0 1 0 6H16zM16 20h6.5a3 3 0 0 1 0 6H16zM16 12v16M19 12v2M19 26v2"/></g></symbol>
    <symbol id="ic-bank" viewBox="0 0 40 40"><g fill="none" stroke="currentColor" stroke-width="1.8" stroke-linejoin="round"><path d="M5 14L20 5l15 9z"/><circle cx="20" cy="10.5" r="1.6"/><path d="M6 16h28M9 18v13M14 18v13M20 18v13M26 18v13M31 18v13M5 33h30M4 36h32"/></g></symbol>
    <symbol id="ic-chart" viewBox="0 0 40 40"><g fill="none" stroke="currentColor" stroke-width="1.8" stroke-linejoin="round"><path d="M5 36h30M7 36V24h5v12M15 36V20h5v16M23 36V22h5v14M31 36V14h4v22"/><path d="M8 18l8-6 7 4 10-10"/><circle cx="8" cy="18" r="1.6"/><circle cx="16" cy="12" r="1.6"/><circle cx="23" cy="16" r="1.6"/><circle cx="33" cy="6" r="1.6"/></g></symbol>
    <symbol id="ic-gift" viewBox="0 0 40 40"><g fill="none" stroke="currentColor" stroke-width="1.8" stroke-linejoin="round"><path d="M10 20h24v16H10zM7 14h30v6H7zM17 14v22M24 14v22"/><path d="M20 14c-3-6-9-7-9-3s6 3 9 3c3 0 9 1 9-3s-6-3-9 3"/></g></symbol>
    <symbol id="ic-annuity" viewBox="0 0 40 40"><g fill="none" stroke="currentColor" stroke-width="1.8" stroke-linecap="round"><circle cx="17" cy="20" r="12"/><path d="M15 5h4M17 5v3M17 20v-7M17 20l5 3"/><circle cx="30" cy="30" r="6"/><path d="M30 26v8M28 28h3a1 1 0 0 1 0 2h-2a1 1 0 0 0 0 2h3"/></g></symbol>
    <symbol id="ic-pin" viewBox="0 0 20 20"><g fill="none" stroke="currentColor" stroke-width="1.6"><path d="M10 18s6-6 6-10a6 6 0 0 0-12 0c0 4 6 10 6 10z"/><circle cx="10" cy="8" r="2.2"/></g></symbol>
    <symbol id="ic-phone" viewBox="0 0 20 20"><g fill="none" stroke="currentColor" stroke-width="1.6"><rect x="5" y="2" width="10" height="16" rx="2"/><path d="M9 15h2"/></g></symbol>
    <symbol id="ic-globe" viewBox="0 0 20 20"><g fill="none" stroke="currentColor" stroke-width="1.4"><circle cx="10" cy="10" r="8"/><ellipse cx="10" cy="10" rx="3.5" ry="8"/><path d="M2 10h16M3.5 6h13M3.5 14h13"/></g></symbol>
  </defs>
</svg>

<!-- OUTSIDE SHEET -->
<section class="sheet sheet--outside">

  <div class="panel impact">
    <h1 class="abs impact__title center">THE IMPACT OF<span>YOUR GIFT</span></h1>
    <p class="abs impact__text center">Your generosity drives our mission. With every Smart gift you’re supporting Meadowlark and Allied Services. Join our community of Smart Givers today and make an enduring impact. With Smart Giving your generosity reaches further. Begin your Smart Giving journey with us today.</p>
    <ul class="abs checklist">
      <li><svg><use href="#ic-check"/></svg>Stocks and Securities</li>
      <li><svg><use href="#ic-check"/></svg>DAFs</li>
      <li><svg><use href="#ic-check"/></svg>QCDs</li>
      <li><svg><use href="#ic-check"/></svg>Crypto</li>
      <li><svg><use href="#ic-check"/></svg>Charitable Annuity</li>
    </ul>
    <svg class="abs" style="top:0;left:0" width="216" height="513" viewBox="0 0 216 513">
      <defs>
        <linearGradient id="g-walk" x1="0" y1="0" x2="1" y2="1">
          <stop offset="0" stop-color="#4d5a3a"/><stop offset=".5" stop-color="#3b4460"/><stop offset="1" stop-color="#6c7a4a"/>
        </linearGradient>
      </defs>
      <path d="M0 348Q100 285 216 340V513H0z" fill="url(#g-walk)" role="img" aria-label="Photo of a younger man walking arm in arm with a smiling older man outdoors"/>
      <path d="M0 342Q100 272 216 334" fill="none" stroke="var(--green)" stroke-width="7"/>
    </svg>
  </div>

  <div class="panel contact">
    <div class="abs brandmark"><i></i><span>Meadowlark and Allied<br>Services, Inc.</span></div>
    <p class="abs contact__intro center">To learn more about Smart Giving Options and how they can benefit you and Meadowlark and Allied Services, please reach out to our team. We’re here to help you navigate these giving methods and answer any question you may have.</p>
    <div class="abs quote center"><em>Being kind to others is a way of being good to yourself.</em><b>Ellen Marsh</b></div>
    <div class="abs quote__mark">“</div>
    <div class="abs will center">
      <p class="will__lead">If you do not have a will</p>
      <p class="will__url">go to www.WillSimple.org</p>
      <p class="will__note">In 20 minutes you can have a</p>
      <p class="will__free">legal will – for free.</p>
    </div>
    <div class="abs pill-contact center">CONTACT US</div>
    <div class="abs contact__ask center"><b>Have more question?</b><span>Please contact us at Meadowlark and Allied Services</span></div>
    <ul class="abs details">
      <li><span class="ic"><svg><use href="#ic-pin"/></svg></span><span>1420 Prairie Ave. Suite 2<br>Millbrook, ND 58000</span></li>
      <li><span class="ic"><svg><use href="#ic-phone"/></svg></span><span>Call us Today!<br><b>555-014-2600</b> (ext. 100)</span></li>
      <li><span class="ic"><svg><use href="#ic-globe"/></svg></span><span>jlarsen@meadowlarkas.org<br><b>www.meadowlarkas.org</b></span></li>
    </ul>
    <div class="abs follow">Follow us <i></i><i></i></div>
    <p class="abs disclaimer center">This material has been prepared for informational purposes only and is not intended to provide tax, accounting, or legal advice. Meadowlark and Allied Services is not a professional fiduciary organization. Please consult with your tax advisor or financial professional before making a decision about Smart Giving.</p>
  </div>

  <div class="panel cover">
    <svg class="abs cover__art" width="227" height="513" viewBox="0 0 227 513">
      <defs>
        <linearGradient id="g-sun" x1="0" y1="0" x2="1" y2="1">
          <stop offset="0" stop-color="#e9d9a6"/><stop offset=".45" stop-color="#b88a62"/><stop offset="1" stop-color="#6f8a3e"/>
        </linearGradient>
      </defs>
      <path d="M0 0H227V168Q120 205 0 180z" fill="url(#g-sun)" role="img" aria-label="Photo of a joyful woman with curly hair laughing in sunlit greenery"/>
      <path d="M0 178Q120 200 227 166" fill="none" stroke="var(--green)" stroke-width="6"/>
      <path d="M0 428Q113 372 227 418V513H0z" fill="var(--white)"/>
      <path d="M2 422Q113 362 225 410" fill="none" stroke="var(--green)" stroke-width="7" stroke-linecap="round"/>
    </svg>
    <h2 class="abs cover__title center">TRANSFORM<span>YOUR GIVING</span></h2>
    <div class="abs cover__ticks"><span><svg><use href="#ic-check"/></svg>Be Strategic</span><span><svg><use href="#ic-check"/></svg>Be Smart</span></div>
    <p class="abs cover__lead center">Discover the impact of Smart Giving with Meadowlark and Allied Services</p>
    <ul class="abs options">
      <li><svg><use href="#ic-coin"/></svg>Crypto</li>
      <li><svg><use href="#ic-bank"/></svg>DAF’s</li>
      <li><svg><use href="#ic-chart"/></svg>Stocks<br>&amp; Securities</li>
      <li><svg><use href="#ic-gift"/></svg>QCDs</li>
      <li><svg><use href="#ic-annuity"/></svg>Charitable Annuity</li>
    </ul>
    <div class="abs brandmark"><i></i><span>Meadowlark and Allied<br>Services, Inc.</span></div>
  </div>
</section>

<!-- INSIDE SHEET -->
<section class="sheet sheet--inside inside">
  <div class="mid-panel"></div>
  <svg class="abs inside__art" width="660" height="200" viewBox="0 0 660 200">
    <defs>
      <linearGradient id="g-hands" x1="0" y1="0" x2="1" y2="0">
        <stop offset="0" stop-color="#c9c3ba"/><stop offset=".5" stop-color="#d8b29a"/><stop offset="1" stop-color="#b9aa98"/>
      </linearGradient>
    </defs>
    <path d="M60 0H660V96C560 138 430 150 320 124C210 98 120 52 60 0z" fill="url(#g-hands)" role="img" aria-label="Photo of a younger hand gently holding an elderly person’s hand"/>
    <path d="M95 112C240 158 400 166 500 108C410 176 230 170 95 112z" fill="var(--green)"/>
  </svg>
  <svg class="abs badge" width="240" height="92" viewBox="0 0 240 92">
    <path d="M40 1H186a38 38 0 0 1 0 76H72l-8 10-6-10H40a38 38 0 0 1 0-76z" fill="var(--navy)" stroke="var(--white)" stroke-width="2"/>
  </svg>
  <div class="abs badge__num">5</div>
  <h2 class="abs badge__text">STRATEGIC<br>AND SMART<br>WAYS</h2>

  <article class="way" style="top:163px;left:18px;width:190px">
    <div class="way__head">
      <div class="way__icon"><svg><use href="#ic-chart"/></svg></div>
      <div class="way__titles"><h2>Gifts of Stocks or Appreciated Assets Strategic &amp; Smart</h2><p>Consider your long-term publicly traded stock as a way to give to your favorite charity.</p></div>
    </div>
    <div class="way__body">
      <p>You can make a significantly bigger impact when you donate long-term appreciated securities, including stock, mutual funds, and bonds, directly to your favorite charity.</p>
      <span class="how">How Does It Work?</span>
      <p>When you donate stock to a charity, you will generally take a tax deduction for the full market value. Because you are donating stock, your contribution and tax deduction may be significantly higher than contributing the after-tax proceeds. The same benefits apply when you donate mutual funds or bonds.</p>
    </div>
  </article>

  <article class="way" style="top:327px;left:18px;width:190px">
    <div class="way__head">
      <div class="way__icon"><svg><use href="#ic-bank"/></svg></div>
      <div class="way__titles"><h2>Donor-Advised<br>Fund (DAF)<br>Strategic &amp; Smart</h2><p>Consider a DAF – a simple, flexible, and tax-advantageous way to give to your favorite charities.</p></div>
    </div>
    <div class="way__body">
      <p>A Donor-Advised Fund (DAF), is like a charitable investment account for the sole purpose of supporting your favorite charities.</p>
      <span class="how">How Does It Work?</span>
      <p>You establish a DAF and contribute cash, stocks, or non-publicly traded assets, cryptocurrency, and private company stock to be eligible for an immediate tax deduction. Those funds are contributed for tax-free growth. You can recommend grants be made from your DAF to any IRS qualified public charity.</p>
    </div>
  </article>

  <article class="way" style="top:172px;left:234px;width:190px">
    <div class="way__head">
      <div class="way__icon"><svg><use href="#ic-coin"/></svg></div>
      <div class="way__titles" style="padding-top:12px"><h2>Cryptocurrency<br>Strategic &amp; Smart</h2><p>Consider donating Bitcoin and other cryptocurrencies to your favorite charity.</p></div>
    </div>
    <div class="way__body">
      <p>Bitcoin and other cryptocurrencies can be donated to charity just like other appreciated assets such as stocks and other business interests. Before you sell bitcoin and donate the after-tax proceeds, consider donating your bitcoin directly to a favorite charity.</p>
      <span class="how">How Does It Work?</span>
      <p>Many donors find it useful to open a Donor-Advised Fund (DAF). This strategy includes two significant benefits, both for you and your favorite charity.</p>
      <ul class="ticks">
        <li><svg><use href="#ic-check"/></svg><span>Your tax deduction will be equal to the fair market value of the donated bitcoin (as determined by a qualified appraisal).</span></li>
        <li><svg><use href="#ic-check"/></svg><span>Your cryptocurrency donation is tax-smart because it may eliminate capital gains taxes on the value / appreciation AND your favorite charity will receive 100% of the value of the contribution.</span></li>
      </ul>
      <p>Often charities are not able to accept direct donations of bitcoin/crypto so using a DAF is a great way to donate these assets.</p>
    </div>
  </article>

  <svg class="abs inside__arc" width="220" height="40" viewBox="0 0 220 40">
    <path d="M0 36Q110 -18 220 32Q110 -4 0 36z" fill="var(--green)"/>
  </svg>
  <div class="abs brandmark"><i></i><span>Meadowlark and Allied<br>Services, Inc.</span></div>

  <article class="way" style="top:135px;left:449px;width:205px">
    <div class="way__head">
      <div class="way__icon"><svg><use href="#ic-gift"/></svg></div>
      <div class="way__titles" style="padding-top:8px"><h2>Qualified Charitable Distributions (QCDs) Strategic &amp; Smart</h2><p>Consider a QCD – when planning your IRA withdrawal strategy…and donate to your favorite charity.</p></div>
    </div>
    <div class="way__body">
      <p>IRA owners at age 70 ½ or over can transfer dollars from their IRA to charity tax-free each year. These transfers known as Qualified Charitable Distributions (QCDs) offer eligible older Americans a great way to easily give to charity.</p>
      <span class="how">How Does It Work?</span>
      <p>Are you 72 and required to take a minimum distribution (RMD) from your IRA but do not need the funds? Consider a Qualified Charitable Distribution. Normally, distributions from a traditional IRA are taxable when received. With a QCD, these distributions become tax-free when paid directly from the IRA to your favorite eligible charity. An IRA owner wishing to make a QCD should contact their IRA trustee, allowing time to complete the transaction before the end of the year to receive the tax benefit.</p>
    </div>
  </article>

  <article class="way" style="top:333px;left:449px;width:205px">
    <div class="way__head">
      <div class="way__icon"><svg><use href="#ic-annuity"/></svg></div>
      <div class="way__titles" style="padding-top:12px"><h2>Charitable Gift Annuity<br>Strategic &amp; Smart</h2><p>Consider establishing a Charitable<br>Gift Annuity</p></div>
    </div>
    <div class="way__body">
      <p style="margin-top:10px">You make a donation to a single charity. The gift is set aside in a reserve account and invested.</p>
      <span class="how">How Does It Work?</span>
      <p>A charitable gift annuity is a contract between a donor and a charity. As a donor, you make a sizable gift to charity using cash, securities, or possibly other assets. This money is then invested. In return, you become eligible to take a partial tax deduction for your donation, plus you receive a fixed stream of income from the charity for the rest of your life (as well as your spouse’s, if you’re giving as a couple), the charity receives the remainder of the gift.</p>
    </div>
  </article>
</section>

</body>
</html>
```